BOLD & MINIMALIST DESIGN NEEDED

We want a very bold but minimalistic business card design that is impactful and utilizes both sides of the business card. Our current logo is included for your use.

We want bold fonts and good use of negative space. We don't want the logo to overpower the design.

Target Market(s)

Professionals who are building new commercial buildings.

Industry/Entity Type

Construction

Contact Information for Business Card

Name, Title, email, office phone, cell phone, website

Font styles to use
Serif
Sans Serif

Requirements
Must have
• Bold design!

```html
<!DOCTYPE html>
<html lang="en">
<head>
<meta charset="utf-8">
<title>Ridgeline — Business Card</title>
<link rel="stylesheet" href="https://fonts.googleapis.com/css2?family=Poppins:wght@400;500;800&display=swap">
<style>
  :root {
    --stage: #26272a;
    --card-white: #ffffff;
    --card-dark: #1f2023;
    --ink: #141414;
    --muted: #5c5c5c;
    --rule-grey: #9a9a9a;
    --green: #82c12a;
    --white: #ffffff;
  }
  * { margin: 0; padding: 0; box-sizing: border-box; }
  html, body {
    width: 1200px; height: 952px; overflow: hidden;
    background: var(--stage);
    font-family: "Poppins", Arial, sans-serif;
  }
  .canvas {
    position: relative; width: 1200px; height: 952px;
    display: flex; flex-direction: column; align-items: center; justify-content: center;
    gap: 60px;
  }
  .card {
    position: relative; width: 640px; height: 366px; overflow: hidden;
    box-shadow: 0 18px 40px rgba(0,0,0,.45);
  }

  /* Wordmark: invented name, one colour, one weight */
  .wordmark { position: absolute; display: flex; align-items: center; gap: 12px; }
  .wordmark__mark { width: 18px; height: 18px; background: var(--green); flex: none; }
  .wordmark__name { font-weight: 800; font-size: 38px; line-height: 1; letter-spacing: -0.5px; }

  /* ---------- Front ---------- */
  .card--front { background: var(--card-white); color: var(--ink); }
  .card__rule { position: absolute; inset: 0; width: 100%; height: 100%; }
  .card--front .wordmark { left: 42px; top: 112px; }
  .card--front .wordmark__name { color: var(--ink); }

  .contact { position: absolute; left: 352px; top: 104px; width: 270px; }
  .contact__name {
    font-size: 20px; font-weight: 500; letter-spacing: 1px; line-height: 1.1; text-transform: uppercase;
  }
  .contact__name strong { font-weight: 800; }
  .contact__title { font-size: 11px; color: var(--muted); margin-top: 3px; }
  .contact__divider { width: 46px; height: 1px; background: var(--rule-grey); margin: 9px 0 12px; }
  .contact__list { list-style: none; }
  .contact__item {
    display: flex; align-items: flex-start; gap: 9px;
    font-size: 11px; color: var(--muted); line-height: 1.35; margin-bottom: 7px;
  }
  .contact__icon {
    flex: none; width: 15px; height: 15px; border-radius: 3px; background: var(--green);
    display: flex; align-items: center; justify-content: center; margin-top: 1px;
  }
  .contact__icon svg { width: 9px; height: 9px; }

  /* ---------- Back ---------- */
  .card--back { background: var(--card-dark); }
  .tab { position: absolute; background: var(--green); }
  .tab--left { left: 0; top: 60px; width: 36px; height: 160px; border-radius: 0 12px 12px 0; }
  .tab--right { right: 0; bottom: 110px; width: 46px; height: 150px; border-radius: 12px 0 0 12px; }
  .card--back .wordmark { left: 50%; top: 50%; transform: translate(-50%, -50%); }
  .card--back .wordmark__name { color: var(--white); font-size: 44px; }
</style>
</head>
<body>
<main class="canvas">

  <section class="card card--front" aria-label="Card front">
    <svg class="card__rule" viewBox="0 0 640 366" aria-hidden="true">
      <line x1="0" y1="300" x2="226" y2="312" stroke="var(--ink)" stroke-width="3"/>
      <polygon points="230,318 560,338 560,344 226,324" fill="var(--green)"/>
    </svg>

    <div class="wordmark">
      <span class="wordmark__mark" aria-hidden="true"></span>
      <span class="wordmark__name">RIDGELINE</span>
    </div>

    <div class="contact">
      <h1 class="contact__name">Daniel R. <strong>Marsh</strong></h1>
      <p class="contact__title">Managing Director</p>
      <div class="contact__divider"></div>
      <ul class="contact__list">
        <li class="contact__item">
          <span class="contact__icon"><svg viewBox="0 0 10 10"><path d="M5 0.5a3.3 3.3 0 0 0-3.3 3.3C1.7 6.3 5 9.5 5 9.5s3.3-3.2 3.3-5.7A3.3 3.3 0 0 0 5 .5zm0 4.6a1.3 1.3 0 1 1 0-2.6 1.3 1.3 0 0 1 0 2.6z" fill="#fff"/></svg></span>
          <span>2170 Harbor Avenue<br>Portland, OR 97201</span>
        </li>
        <li class="contact__item">
          <span class="contact__icon"><svg viewBox="0 0 10 10"><path d="M2.2 .8l1.6 1.9-.9 1.2a6 6 0 0 0 3.2 3.2l1.2-.9 1.9 1.6-.9 1.4C4.6 9.2.8 5.4.8 1.7z" fill="#fff"/></svg></span>
          <span>+00 555 019 42</span>
        </li>
        <li class="contact__item">
          <span class="contact__icon"><svg viewBox="0 0 10 10"><rect x="1" y="2" width="8" height="6" fill="none" stroke="#fff" stroke-width="1.1"/><path d="M1 2.3l4 3 4-3" fill="none" stroke="#fff" stroke-width="1.1"/></svg></span>
          <span>office@ridgelinebuild.com</span>
        </li>
        <li class="contact__item">
          <span class="contact__icon"><svg viewBox="0 0 10 10"><path d="M5 1L9 6H6.3v3H3.7V6H1z" fill="#fff"/></svg></span>
          <span>www.ridgelinebuild.com</span>
        </li>
      </ul>
    </div>
  </section>

  <section class="card card--back" aria-label="Card back">
    <span class="tab tab--left" aria-hidden="true"></span>
    <span class="tab tab--right" aria-hidden="true"></span>
    <div class="wordmark">
      <span class="wordmark__mark" aria-hidden="true"></span>
      <span class="wordmark__name">RIDGELINE</span>
    </div>
  </section>

</main>
</body>
</html>
```